Letter and Envelope Design For Harborline Realty

Please design a letter and an envelope incorporating our logo (See Attached). We are also launched a business card contest. Since we want them to match, please feel free to submit a design for both the business card and also the letter design and envelope.

Requirements
Must have
• The envelope, the letter and the business cards must match somehow connecting the designs. We want them to have something that holds them together besides the logo.

```html
<!DOCTYPE html>
<html lang="en">
<head>
<meta charset="utf-8">
<title>Harborline Realty Stationery</title>
<link href="https://fonts.googleapis.com/css2?family=Josefin+Sans:wght@600&family=Source+Sans+3:wght@400;600&display=swap" rel="stylesheet">
<style>
  :root {
    --backdrop: #878787;
    --paper: #ffffff;
    --ink: #3a3a3a;
    --ink-soft: #5a5a5a;
    --charcoal: #3d3d3d;
    --charcoal-light: #585858;
    --band: #3a3a3a;
  }
  * { margin: 0; padding: 0; box-sizing: border-box; }
  html, body { width: 1200px; height: 1200px; overflow: hidden; }
  body { background: var(--backdrop); font-family: "Source Sans 3", sans-serif; color: var(--ink); position: relative; }

  .sheet { position: absolute; background: var(--paper); }
  .sheet::after { content: ""; position: absolute; left: 0; right: 0; bottom: 0; height: 9px; background: var(--band); }

  .brand { display: flex; flex-direction: column; align-items: center; gap: 10px; }
  .brand-ring { border: 3px solid var(--ink); border-radius: 50%; }
  .brand-name { font-family: "Josefin Sans", sans-serif; font-weight: 600; color: var(--ink); letter-spacing: 0.12em; text-transform: uppercase; white-space: nowrap; }

  .contact-icon { width: 16px; height: 16px; background: var(--charcoal); display: inline-flex; align-items: center; justify-content: center; flex-shrink: 0; }
  .contact-icon svg { width: 10px; height: 10px; }

  /* Letterhead */
  .letterhead { left: 76px; top: 101px; width: 706px; height: 997px; }
  .letterhead .brand { position: absolute; top: 32px; left: 0; right: 0; }
  .letterhead .brand-ring { width: 96px; height: 96px; }
  .letterhead .brand-name { font-size: 22px; }
  .letterhead-footer { position: absolute; bottom: 30px; left: 0; right: 0; display: flex; flex-direction: column; align-items: center; gap: 10px; font-size: 12.5px; color: var(--ink-soft); }
  .footer-row { display: flex; gap: 12px; align-items: center; }
  .contact-item { display: flex; align-items: center; gap: 10px; }

  /* Business card front */
  .card-front { left: 689px; top: 102px; width: 449px; height: 262px; }
  .card-front .brand { position: absolute; left: 14px; width: 190px; top: 80px; }
  .card-front .brand-ring { width: 70px; height: 70px; }
  .card-front .brand-name { font-size: 13px; }
  .card-divider { position: absolute; left: 213px; top: 46px; width: 1px; height: 166px; background: var(--ink-soft); }
  .card-person { position: absolute; left: 230px; top: 44px; }
  .person-name { font-size: 17px; font-weight: 600; color: var(--ink); }
  .person-role { font-size: 13px; color: var(--ink-soft); margin-top: 2px; }
  .card-contacts { position: absolute; left: 230px; top: 118px; display: flex; flex-direction: column; gap: 9px; font-size: 11.5px; color: var(--ink-soft); }
  .card-contacts .contact-item { gap: 12px; }
  .card-contacts .contact-item:first-child { font-size: 13px; }

  /* Business card back */
  .card-back { position: absolute; left: 689px; top: 401px; width: 449px; height: 262px; background: radial-gradient(circle at 50% 50%, var(--charcoal-light), var(--charcoal) 70%); display: flex; align-items: center; justify-content: center; }
  .card-back .brand-ring { border-color: #fff; width: 92px; height: 92px; }
  .card-back .brand-name { color: #fff; font-size: 15px; }

  /* Envelope */
  .envelope-flap { position: absolute; left: 600px; top: 684px; width: 586px; height: 80px; background: radial-gradient(ellipse at 35% 40%, #5e5e5e, var(--charcoal) 75%); clip-path: polygon(4% 0, 96% 0, 100% 100%, 0 100%); border-radius: 14px 14px 0 0; }
  .envelope { left: 600px; top: 762px; width: 586px; height: 276px; }
  .envelope::after { height: 6px; }
  .envelope .brand { position: absolute; left: 20px; width: 140px; top: 12px; gap: 6px; }
  .envelope .brand-ring { width: 52px; height: 52px; border-width: 2px; }
  .envelope .brand-name { font-size: 11px; }
  .envelope-divider { position: absolute; left: 432px; top: 24px; width: 1px; height: 56px; background: var(--ink-soft); }
  .envelope-contacts { position: absolute; left: 440px; top: 25px; display: flex; flex-direction: column; gap: 4px; font-size: 8px; color: var(--ink); }
  .envelope-contacts .contact-item { gap: 8px; }
  .envelope-contacts .contact-icon { width: 10px; height: 10px; }
  .envelope-contacts .contact-icon svg { width: 7px; height: 7px; }
</style>
</head>
<body>

<svg width="0" height="0" style="position:absolute">
  <defs>
    <symbol id="icon-pin" viewBox="0 0 10 10"><path d="M5 1a3 3 0 0 1 3 3c0 2-3 5-3 5S2 6 2 4a3 3 0 0 1 3-3z" fill="none" stroke="#fff" stroke-width="1"/><circle cx="5" cy="4" r="1" fill="#fff"/></symbol>
    <symbol id="icon-phone" viewBox="0 0 10 10"><rect x="1" y="2" width="8" height="2" rx="1" fill="#fff"/><rect x="2.5" y="4" width="5" height="4.5" fill="#fff"/></symbol>
    <symbol id="icon-mail" viewBox="0 0 10 10"><rect x="1" y="2.5" width="8" height="5.5" fill="none" stroke="#fff" stroke-width="1"/><path d="M1 2.5l4 3 4-3" fill="none" stroke="#fff" stroke-width="1"/></symbol>
    <symbol id="icon-web" viewBox="0 0 10 10"><circle cx="5" cy="5" r="4" fill="none" stroke="#fff" stroke-width="0.9"/><ellipse cx="5" cy="5" rx="1.8" ry="4" fill="none" stroke="#fff" stroke-width="0.8"/><path d="M1 5h8" stroke="#fff" stroke-width="0.8"/></symbol>
  </defs>
</svg>

<section class="sheet letterhead">
  <div class="brand">
    <div class="brand-ring"></div>
    <div class="brand-name">Harborline Realty</div>
  </div>
  <footer class="letterhead-footer">
    <div class="contact-item"><span class="contact-icon"><svg><use href="#icon-pin"/></svg></span>Harborline Realty</div>
    <div class="footer-row">
      <div class="contact-item"><span class="contact-icon"><svg><use href="#icon-phone"/></svg></span>312-555-0148</div>
      <div class="contact-item"><span class="contact-icon"><svg><use href="#icon-mail"/></svg></span>info@harborline-realty.com</div>
      <div class="contact-item"><span class="contact-icon"><svg><use href="#icon-web"/></svg></span>www.harborline-realty.com</div>
    </div>
  </footer>
</section>

<section class="sheet card-front">
  <div class="brand">
    <div class="brand-ring"></div>
    <div class="brand-name">Harborline Realty</div>
  </div>
  <div class="card-divider"></div>
  <div class="card-person">
    <div class="person-name">Daniel Reyes</div>
    <div class="person-role">Realtor</div>
  </div>
  <div class="card-contacts">
    <div class="contact-item"><span class="contact-icon"><svg><use href="#icon-pin"/></svg></span>Harborline Realty</div>
    <div class="contact-item"><span class="contact-icon"><svg><use href="#icon-phone"/></svg></span>312-555-0148</div>
    <div class="contact-item"><span class="contact-icon"><svg><use href="#icon-mail"/></svg></span>info@harborline-realty.com</div>
    <div class="contact-item"><span class="contact-icon"><svg><use href="#icon-web"/></svg></span>www.harborline-realty.com</div>
  </div>
</section>

<section class="card-back">
  <div class="brand">
    <div class="brand-ring"></div>
    <div class="brand-name">Harborline Realty</div>
  </div>
</section>

<div class="envelope-flap"></div>
<section class="sheet envelope">
  <div class="brand">
    <div class="brand-ring"></div>
    <div class="brand-name">Harborline Realty</div>
  </div>
  <div class="envelope-divider"></div>
  <div class="envelope-contacts">
    <div class="contact-item"><span class="contact-icon"><svg><use href="#icon-pin"/></svg></span>Harborline Realty</div>
    <div class="contact-item"><span class="contact-icon"><svg><use href="#icon-phone"/></svg></span>312-555-0148</div>
    <div class="contact-item"><span class="contact-icon"><svg><use href="#icon-mail"/></svg></span>info@harborline-realty.com</div>
    <div class="contact-item"><span class="contact-icon"><svg><use href="#icon-web"/></svg></span>www.harborline-realty.com</div>
  </div>
</section>

</body>
</html>
```